Redesign of business card for Cedar Ridge Mechanical

We are looking for a new design for our business cards for Cedar Ridge Mechanical. We are a plumbing & HVAC construction company, operating on the West Coast of Canada and USA. Logo attached.
Industry/Entity Type
Construction - Plumbing & HVAC
Contact Information for Business Card
Name, address, phone numbers, email, website address
Look and feel
Each slider illustrates characteristics of the customer's brand and the style your logo design should communicate.

```html
<!DOCTYPE html>
<html lang="en">
<head>
<meta charset="utf-8">
<title>Cedar Ridge Mechanical – Business Card</title>
<link rel="stylesheet" href="https://fonts.googleapis.com/css2?family=Montserrat:wght@400;500;700&display=swap">
<style>
  :root {
    --page-bg: #e7e3dd;
    --card-light: #efe9df;
    --card-light-edge: #e2dace;
    --card-dark: #2b2927;
    --card-dark-deep: #1f1d1c;
    --stripe-light: #b9b2a8;
    --stripe-dark: #6f6a64;
    --gold: #d9c7a6;
    --gold-soft: #cdbb98;
    --ink: #242220;
  }
  * { margin: 0; padding: 0; box-sizing: border-box; }
  html, body {
    width: 1200px;
    height: 1047px;
    overflow: hidden;
    background: var(--page-bg);
    font-family: "Montserrat", Arial, sans-serif;
  }
  .card {
    position: absolute;
    left: 100px;
    top: 251px;
    width: 1000px;
    height: 545px;
    border-radius: 22px;
    overflow: hidden;
    background: linear-gradient(160deg, var(--card-light), var(--card-light-edge));
    box-shadow: 0 18px 40px rgba(0,0,0,0.18);
  }
  .card-waves { position: absolute; inset: 0; width: 100%; height: 100%; }
  .brand {
    position: absolute;
    right: 40px;
    top: 92px;
    display: flex;
    align-items: center;
    gap: 16px;
    color: var(--ink);
    font-weight: 700;
    font-size: 30px;
    letter-spacing: 0.5px;
    text-transform: uppercase;
  }
  .brand-square { width: 26px; height: 26px; background: var(--ink); }
  .person { position: absolute; left: 43px; top: 246px; }
  .person-name {
    color: var(--gold);
    font-weight: 700;
    font-size: 34px;
    letter-spacing: 0.6px;
  }
  .person-role {
    margin-top: 6px;
    color: var(--gold-soft);
    font-weight: 400;
    font-size: 24px;
    letter-spacing: 0.6px;
  }
  .contact-list {
    position: absolute;
    left: 43px;
    top: 404px;
    list-style: none;
  }
  .contact-item {
    display: flex;
    align-items: center;
    gap: 14px;
    height: 38px;
    color: var(--gold);
    font-size: 25px;
    font-weight: 400;
  }
  .contact-icon { width: 20px; height: 20px; flex: none; }
  .address {
    position: absolute;
    right: 39px;
    top: 440px;
    text-align: right;
    color: var(--gold);
    font-size: 25px;
    line-height: 39px;
    font-style: normal;
  }
</style>
</head>
<body>
  <main class="card">
    <svg class="card-waves" viewBox="0 0 1000 545" preserveAspectRatio="none" aria-hidden="true">
      <defs>
        <linearGradient id="stripeShade" x1="0" y1="0" x2="1" y2="0">
          <stop offset="0" stop-color="var(--stripe-dark)"/>
          <stop offset="0.5" stop-color="var(--stripe-light)"/>
          <stop offset="1" stop-color="var(--stripe-dark)"/>
        </linearGradient>
        <linearGradient id="darkShade" x1="0" y1="0" x2="0" y2="1">
          <stop offset="0" stop-color="var(--card-dark)"/>
          <stop offset="1" stop-color="var(--card-dark-deep)"/>
        </linearGradient>
      </defs>
      <path class="wave-stripe" fill="url(#stripeShade)"
            d="M260 160 C 470 170, 690 360, 1000 330 L1000 372 C 700 385, 480 215, 260 172 Z"/>
      <path class="wave-dark" fill="url(#darkShade)"
            d="M0 215 C 80 168, 200 150, 300 168 C 500 205, 700 390, 1000 368 L1000 545 L0 545 Z"/>
    </svg>

    <div class="brand">
      <span class="brand-square"></span>
      <span class="brand-name">Cedar Ridge Mechanical</span>
    </div>

    <div class="person">
      <h1 class="person-name">MARTIN COLE</h1>
      <p class="person-role">OWNER</p>
    </div>

    <ul class="contact-list">
      <li class="contact-item">
        <svg class="contact-icon" viewBox="0 0 24 24" fill="var(--gold)"><path d="M6.6 10.8a15.1 15.1 0 0 0 6.6 6.6l2.2-2.2a1 1 0 0 1 1-.25 11.4 11.4 0 0 0 3.6.57 1 1 0 0 1 1 1V20a1 1 0 0 1-1 1A17 17 0 0 1 3 4a1 1 0 0 1 1-1h3.5a1 1 0 0 1 1 1c0 1.25.2 2.45.57 3.57a1 1 0 0 1-.25 1z"/></svg>
        <span>123 456 789</span>
      </li>
      <li class="contact-item">
        <svg class="contact-icon" viewBox="0 0 24 24" fill="none" stroke="var(--gold)" stroke-width="2"><rect x="3" y="5" width="18" height="14" rx="1"/><path d="M3 6l9 7 9-7"/></svg>
        <span>info@yourgmail.com</span>
      </li>
      <li class="contact-item">
        <svg class="contact-icon" viewBox="0 0 24 24" fill="none" stroke="var(--gold)" stroke-width="2"><circle cx="12" cy="12" r="9"/><path d="M3 12h18M12 3c3 3.5 3 14.5 0 18M12 3c-3 3.5-3 14.5 0 18"/></svg>
        <span>www.yourwebsite.com</span>
      </li>
    </ul>

    <address class="address">
      Your address, City<br>
      State, Zip 1234
    </address>
  </main>
</body>
</html>
```